Updates

Please take these words out of the flyer " or any other fees whatsoever." Added Monday, August 8, 2016

Industry/Entity Type

Real Estate

Font styles to use
Serif

Requirements
Must have

```html
<!DOCTYPE html>
<html lang="en">
<head>
<meta charset="utf-8">
<title>Summit Crest Realty – Commission Plans Flyer</title>
<link href="https://fonts.googleapis.com/css2?family=PT+Serif:wght@400;700&display=swap" rel="stylesheet">
<style>
  :root {
    --backdrop: #b1b1b1;
    --paper: #ffffff;
    --red: #e11d25;
    --red-deep: #c31a21;
    --slate: #5e5f62;
    --ink: #1a1a1a;
    --white: #ffffff;
  }
  * { margin: 0; padding: 0; box-sizing: border-box; }
  html, body { width: 900px; height: 1200px; overflow: hidden; }
  body { background: var(--backdrop); font-family: "PT Serif", Georgia, serif; position: relative; }

  .flyer { position: absolute; left: 140px; top: 160px; width: 625px; height: 883px; background: var(--paper); overflow: hidden; }
  .red-field { position: absolute; left: 0; top: 290px; width: 625px; height: 540px; }

  .brand-mark { position: absolute; left: 0; top: 130px; width: 625px; text-align: center;
    font-weight: 700; font-size: 34px; color: var(--slate); }
  .brand-mark .dot { display: inline-block; width: 18px; height: 18px; background: var(--red); margin-right: 12px; vertical-align: 2px; }

  .company { position: absolute; left: 0; top: 306px; width: 625px; text-align: center; color: var(--white); font-weight: 700; font-size: 28px; line-height: 36px; }
  .tagline { position: absolute; left: 0; top: 345px; width: 625px; text-align: center; color: var(--white); font-weight: 700; font-size: 14px; }

  .plans-title { position: absolute; left: 77px; top: 381px; width: 464px; height: 52px; border-radius: 10px; background: var(--slate);
    color: var(--white); font-weight: 700; font-size: 27px; line-height: 52px; text-align: center; }

  .plan-tag { position: absolute; left: 259px; width: 106px; height: 46px; border: 1.5px solid var(--white); border-radius: 8px;
    color: var(--white); font-weight: 700; text-align: center; line-height: 44px; font-size: 14px; white-space: nowrap; }
  .plan-tag .num { font-size: 22px; }
  .plan-one { top: 459px; }
  .plan-two { top: 562px; }
  .plan-three { top: 666px; }

  .plan-text { position: absolute; left: 0; width: 625px; text-align: center; color: var(--white); font-weight: 700; font-size: 16px; line-height: 20px; }
  .plan-text .price { font-size: 23px; }
  .text-one { top: 521px; }
  .text-two { top: 627px; }
  .text-three { top: 731px; }

  .portrait { position: absolute; left: 20px; top: 678px; width: 90px; height: 120px; border: 3px solid var(--white);
    background: linear-gradient(160deg, #8a8f96, #4a4c50 60%, #6b2a2e); }

  .name-tag { position: absolute; left: 0; top: 798px; width: 275px; height: 27px; }
  .name-tag svg { position: absolute; left: 0; top: 0; }
  .name-tag p { position: absolute; left: 22px; top: 4px; font-weight: 700; font-size: 14px; color: var(--red); white-space: nowrap; }
  .name-tag .role { color: var(--ink); font-size: 16px; margin-left: 4px; }

  .social { position: absolute; left: 502px; top: 796px; display: flex; gap: 9px; }
  .social span { width: 18px; height: 18px; background: var(--white); border-radius: 3px; }

  .footer { position: absolute; left: 0; top: 821px; width: 625px; height: 62px; background: var(--slate); color: var(--white); }
  .footer .line { position: absolute; left: 20px; font-size: 11px; font-weight: 700; display: flex; align-items: center; gap: 9px; white-space: nowrap; }
  .footer .address { top: 12px; }
  .footer .web { top: 36px; }
  .footer .divider { position: absolute; left: 359px; top: 7px; width: 1px; height: 46px; background: var(--white); }
  .footer .phone { position: absolute; left: 372px; top: 12px; display: flex; align-items: center; gap: 12px; font-size: 28px; font-weight: 700; white-space: nowrap; }
</style>
</head>
<body>
<main class="flyer">
  <div class="brand-mark"><span class="dot"></span>Summit Crest Realty</div>

  <svg class="red-field" width="625" height="540" viewBox="0 0 625 540" aria-hidden="true">
    <defs>
      <linearGradient id="redSweep" x1="0" x2="1" y1="0" y2="0">
        <stop offset="0" stop-color="#c31a21"/>
        <stop offset="0.5" stop-color="#e11d25"/>
        <stop offset="1" stop-color="#c31a21"/>
      </linearGradient>
    </defs>
    <path d="M0 40 Q312 -30 625 40 L625 540 L0 540 Z" fill="url(#redSweep)"/>
  </svg>

  <h1 class="company">Summit Crest Realty</h1>
  <p class="tagline">Your Key To Real Estate</p>

  <h2 class="plans-title">OUR 3 COMMISSION PLANS</h2>

  <div class="plan-tag plan-one"><span class="num">1</span>ST PLANE</div>
  <p class="plan-text text-one">100% commision 99 dollars a month and <span class="price">$249</span> per transaction</p>

  <div class="plan-tag plan-two"><span class="num">2</span>ND PLANE</div>
  <p class="plan-text text-two">90/10 for <span class="price">$69</span> per month</p>

  <div class="plan-tag plan-three"><span class="num">3</span>RD PLANE</div>
  <p class="plan-text text-three">80/20 all planshave no office fees,<br>no franchise fees.</p>

  <div class="portrait" role="img" aria-label="Portrait photo of the broker owner"></div>

  <div class="name-tag">
    <svg width="275" height="27" viewBox="0 0 275 27" aria-hidden="true">
      <polygon points="263,0 275,14 263,14" fill="#5e5f62"/>
      <rect x="0" y="0" width="263" height="27" fill="#ffffff"/>
    </svg>
    <p>Marian Holt , <span class="role">Broker Owner</span></p>
  </div>

  <div class="social" aria-label="Social media links"><span></span><span></span><span></span><span></span></div>

  <footer class="footer">
    <p class="line address">
      <svg width="11" height="15" viewBox="0 0 11 15" aria-hidden="true"><path d="M5.5 0C2.5 0 0 2.4 0 5.4 0 9.3 5.5 15 5.5 15S11 9.3 11 5.4C11 2.4 8.5 0 5.5 0Zm0 7.6a2.2 2.2 0 1 1 0-4.4 2.2 2.2 0 0 1 0 4.4Z" fill="#ffffff"/></svg>
      4820 Cedar Hollow Rd, Lakeview, TX 75501 1st floor 210
    </p>
    <p class="line web">
      <svg width="12" height="12" viewBox="0 0 12 12" aria-hidden="true" fill="none" stroke="#ffffff" stroke-width="1.2"><circle cx="6" cy="6" r="5.2"/><ellipse cx="6" cy="6" rx="2.3" ry="5.2"/><path d="M0.8 6h10.4"/></svg>
      www.marianholt.com
    </p>
    <span class="divider"></span>
    <p class="phone">
      <svg width="22" height="22" viewBox="0 0 24 24" aria-hidden="true"><path d="M6.6 10.8a15 15 0 0 0 6.6 6.6l2.2-2.2a1 1 0 0 1 1-.25 11.4 11.4 0 0 0 3.6.57 1 1 0 0 1 1 1V20a1 1 0 0 1-1 1A17 17 0 0 1 3 4a1 1 0 0 1 1-1h3.5a1 1 0 0 1 1 1c0 1.25.2 2.45.57 3.57a1 1 0 0 1-.25 1Z" fill="#ffffff"/></svg>
      555-204-7731
    </p>
  </footer>
</main>
</body>
</html>
```